Website Refresh

I'm looking to refresh my Squarespace website. www.derekmulvane.com

I am pretty happy with the content but would like a better navigation bar, livelier color choices, consistent type faces, and a more modern look. I am willing to pay extra to implement suggested improvements that would make the site more appealing

```html
<!DOCTYPE html>
<html lang="en">
<head>
<meta charset="utf-8">
<title>Peerhold – Private Advisory Boards for CEOs</title>
<link href="https://fonts.googleapis.com/css2?family=IBM+Plex+Sans:wght@400;500;600;700&family=Lato:wght@300;400;700&display=swap" rel="stylesheet">
<style>
:root{
  --navy:#0e2c4e;
  --navy-deep:#0b2540;
  --blue:#1766bf;
  --orange:#e64a1d;
  --ink:#1b1b1b;
  --muted:#444;
  --gray-bg:#f1f3f8;
  --line:#d6d9e0;
  --white:#fff;
}
*{box-sizing:border-box;margin:0;padding:0}
html,body{width:1200px;height:4878px;overflow:hidden;background:var(--white)}
body{font-family:"Lato",sans-serif;color:var(--ink);position:relative}
.abs{position:absolute}
.head{font-family:"IBM Plex Sans",sans-serif}
.btn{position:absolute;background:var(--orange);color:var(--white);font-family:"IBM Plex Sans",sans-serif;font-weight:600;font-size:13px;letter-spacing:.5px;display:flex;align-items:center;justify-content:center;text-transform:uppercase}
.brand{font-family:"IBM Plex Sans",sans-serif;font-weight:700;color:var(--navy);letter-spacing:-1px}
.brand-sub{font-size:10px;color:#555;line-height:1.2}
.nav{position:absolute;left:0;top:91px;width:1200px;height:40px;background:var(--blue);display:flex;align-items:center;padding-left:134px;gap:28px}
.nav a{color:var(--white);font-family:"IBM Plex Sans",sans-serif;font-size:11px;font-weight:600;text-decoration:none;letter-spacing:.3px}
.photo{position:absolute}
.center{text-align:center;width:1200px;left:0}
.h2{font-family:"IBM Plex Sans",sans-serif;font-weight:600;font-size:22px;letter-spacing:.3px;color:var(--ink)}
.lede{font-weight:300;font-size:18px;line-height:29px;color:var(--muted)}
.labelbox{position:absolute;border:1px solid var(--line);background:var(--white);font-family:"IBM Plex Sans",sans-serif;font-weight:500;display:flex;align-items:center;justify-content:center}
.card{position:absolute;top:1478px;width:223px;height:161px;background:var(--white);box-shadow:0 2px 6px rgba(0,0,0,.08);text-align:center;font-size:13px;line-height:21px;color:#333}
.card svg{display:block;margin:26px auto 14px}
.body-txt{font-size:14px;line-height:22.5px;color:#222}
.award{position:absolute;top:2432px;font-size:12.5px;line-height:21px;color:#333}
.divider{position:absolute;top:2435px;width:1px;height:120px;background:var(--line)}
.post{position:absolute;top:3142px;width:299px;height:383px;background:var(--white)}
.post .img{height:171px}
.post .in{padding:24px 26px 0}
.post .date{font-size:11px;text-decoration:underline;color:#333}
.post h3{font-family:"Lato",sans-serif;font-weight:400;font-size:15px;line-height:22px;margin:8px 0 10px;color:#111}
.post p{font-size:11px;line-height:17px;color:#444}
.post .btn{position:static;width:82px;height:24px;font-size:9px;margin-top:14px}
.fnav{position:absolute;top:4743px;left:134px;display:flex;gap:28px}
.fnav a{color:#cfd8e4;font-family:"IBM Plex Sans",sans-serif;font-size:11px;text-decoration:none}
</style>
</head>
<body>

<!-- Header -->
<header>
  <div class="abs" style="left:132px;top:16px">
    <div class="brand" style="font-size:34px;line-height:34px">PEERHOLD</div>
    <div class="brand-sub" style="margin-left:6px;margin-top:2px">Private advisory boards for CEOs,<br>executives and business owners.</div>
  </div>
  <div class="abs head" style="left:777px;top:39px;font-size:11px;font-weight:600">FOLLOW US</div>
  <div class="abs" style="left:855px;top:29px;width:32px;height:32px;border-radius:50%;background:var(--navy)"></div>
  <div class="btn" style="left:908px;top:26px;width:159px;height:42px">
    <svg width="12" height="12" viewBox="0 0 24 24" style="margin-right:8px"><path fill="#fff" d="M6.6 10.8a15 15 0 0 0 6.6 6.6l2.2-2.2c.3-.3.7-.4 1-.2 1.1.4 2.3.6 3.6.6.6 0 1 .4 1 1V20c0 .6-.4 1-1 1A17 17 0 0 1 3 4c0-.6.4-1 1-1h3.5c.6 0 1 .4 1 1 0 1.3.2 2.5.6 3.6.1.3 0 .7-.2 1z"/></svg>Contact Derek</div>
</header>
<nav class="nav">
  <a>ABOUT THE GROUP</a><a>MEMBER VIDEO TESTIMONIALS</a><a>TESTIMONIALS</a><a>SUCCESS STORIES</a><a>DEREK'S BLOG</a><a>DEREK MULVANE BIO</a><a>JOIN THE GROUP</a>
</nav>

<!-- Hero -->
<section class="photo" style="left:0;top:131px;width:1200px;height:579px;background:linear-gradient(135deg,#5c6470 0%,#3b3a3a 45%,#6b5a4c 75%,#2d2a28 100%)" role="img" aria-label="CEO advisory board meeting around a conference table with a speaker at a flip chart">
  <div class="head" style="position:absolute;left:246px;top:56px;color:#fff;font-weight:700;font-size:38px;line-height:44px;text-shadow:0 2px 4px rgba(0,0,0,.4)">PRIVATE ADVISORY<br>BOARDS FOR CEOS</div>
  <div class="btn" style="left:249px;top:158px;width:116px;height:44px;font-size:13px">Read More</div>
  <div style="position:absolute;left:562px;top:536px;display:flex;gap:8px;align-items:center">
    <span style="width:6px;height:6px;border-radius:50%;background:#ddd"></span>
    <span style="width:6px;height:6px;border-radius:50%;background:#ddd"></span>
    <span style="width:10px;height:10px;border-radius:50%;background:var(--orange)"></span>
    <span style="width:6px;height:6px;border-radius:50%;background:#ddd"></span>
    <span style="width:6px;height:6px;border-radius:50%;background:#ddd"></span>
  </div>
</section>

<!-- Intro -->
<section>
  <div class="abs center h2" style="top:764px">TURNING GOOD CEOS INTO GREAT CEOS</div>
  <div class="abs center lede" style="top:808px">Our award winning CEOs will help you make better decisions<br>for your company, family, and community .</div>
  <div class="photo" style="left:246px;top:899px;width:708px;height:398px;background:linear-gradient(135deg,#6f7c6a,#4a5a64 50%,#2a3e76);box-shadow:0 3px 8px rgba(0,0,0,.2)" role="img" aria-label="Video still of a member speaking to camera">
    <svg width="24" height="26" viewBox="0 0 24 26" style="position:absolute;left:342px;top:186px"><path d="M0 0L24 13L0 26z" fill="#fff"/></svg>
    <div style="position:absolute;left:0;top:184px;width:26px;height:32px;background:rgba(255,255,255,.25)"></div>
    <svg width="10" height="16" style="position:absolute;left:8px;top:192px"><path d="M8 1L2 8l6 7" stroke="#fff" fill="none" stroke-width="1.5"/></svg>
    <div style="position:absolute;right:0;top:184px;width:26px;height:32px;background:rgba(255,255,255,.25)"></div>
    <svg width="10" height="16" style="position:absolute;right:8px;top:192px"><path d="M2 1l6 7-6 7" stroke="#fff" fill="none" stroke-width="1.5"/></svg>
    <div style="position:absolute;left:12px;bottom:10px;color:#eee;font-size:11px">Martin Halvers</div>
  </div>
</section>

<!-- Membership criteria -->
<section class="abs" style="left:0;top:1352px;width:1200px;height:338px;background:var(--gray-bg)">
  <div class="labelbox" style="left:353px;top:45px;width:494px;height:42px;font-size:15px">MEMBERSHIP IS BY INVITATION ONLY FOR THOSE WHO:</div>
</section>
<div class="card" style="left:131px">
  <svg width="52" height="46" viewBox="0 0 52 46" fill="none" stroke="#333" stroke-width="1.6"><path d="M8 22h8v20H8zM16 24l8-12 2-8c3 0 4 3 3 7l-2 5h11c3 0 4 3 2 5 2 1 2 4 0 5 1 2 0 4-2 5 0 2-1 4-4 4H16"/><path d="M30 2v4M36 4l-2 3M24 4l2 3"/></svg>
  Open to being<br>challenged</div>
<div class="card" style="left:369px">
  <svg width="54" height="46" viewBox="0 0 54 46" fill="none" stroke="#333" stroke-width="1.6"><rect x="4" y="4" width="46" height="32"/><path d="M2 40h50M10 30l10-10 8 6 14-14M36 12h6v6"/><path d="M12 30v4M20 26v8M28 30v4M36 24v10"/></svg>
  Commit to<br>double-digit growth</div>
<div class="card" style="left:608px">
  <svg width="48" height="46" viewBox="0 0 48 46" fill="none" stroke="#333" stroke-width="1.6"><path d="M44 2L4 18l12 6 4 14 6-10 12 6z"/><path d="M16 24L44 2M20 38c-4 2-8 4-12 6" stroke-dasharray="3 3"/></svg>
  Ongoing learning</div>
<div class="card" style="left:846px">
  <svg width="52" height="46" viewBox="0 0 52 46" fill="none" stroke="#333" stroke-width="1.6"><rect x="6" y="8" width="34" height="30"/><path d="M12 16h20M12 22h20M12 28h14M44 4l4 4-18 18h-4v-4z"/></svg>
  Giving &amp; receiving<br>honest feedback.</div>

<!-- Lonely CEO -->
<section>
  <div class="abs center h2" style="top:1748px;font-size:18px;line-height:29px">IF YOU ARE LONELY WITH NO ONE YOU CAN TRUST TO TALK THROUGH TOUGH<br>DECISIONS IF YOU DON'T HAVE THE RIGHT PEOPLE IN THE RIGHT SEATS</div>
  <div class="abs center lede" style="top:1820px;font-size:17px">If you seek financial independence, professional and personal growth, and<br>avoiding burnout; our group might be right for you.</div>
  <div class="photo" style="left:132px;top:1925px;width:512px;height:360px;background:linear-gradient(160deg,#d9dbdc,#9aa0a4 55%,#5b5f63)" role="img" aria-label="Executives in discussion around a boardroom table"></div>
  <div class="abs body-txt" style="left:689px;top:1940px;width:350px">After many years in the business world as the founder/CEO of six for-profit and five not-for-profit corporations, I understand the huge responsibility you have for making the right decisions for your company, the personal well-being of your employees and yourself.<br><br>Our Peerhold group is made up of 15 other smart CEOs who have been where you are. We meet monthly in a safe, confidential environment to discuss critical business decisions, opportunities, and challenges. Additionally I meet with each member two hours/monthly for a private coaching session.</div>
</section>

<!-- Awards -->
<section>
  <div class="labelbox" style="left:343px;top:2347px;width:514px;height:42px;font-size:12.5px;font-weight:600">OUR BEST-IN-CLASS MEMBERS HAVE RECEIVED THE FOLLOWING AWARDS:</div>
  <div class="award" style="left:132px;top:2462px;width:160px">K &amp; M Entrepreneur of the Year Finalists</div>
  <div class="divider" style="left:318px"></div>
  <div class="award" style="left:356px;top:2462px;width:170px">Venture Monthly Fastest Growing 500 and 5000 and Most Admired CEO Finalists</div>
  <div class="divider" style="left:561px"></div>
  <div class="award" style="left:594px;top:2462px;width:190px">Founder Weekly Top Company Cultures</div>
  <div class="divider" style="left:798px"></div>
  <div class="award" style="left:835px;width:220px">Harbor Business Review's Fastest Growing 100: Most Admired CEO, Most Admired Family Businesses, Healthiest Companies, Best Place to Work and Military Entrepreneurs Award Winners</div>
</section>

<!-- Peer CEOs -->
<section class="abs" style="left:0;top:2618px;width:1200px;height:403px;background:var(--gray-bg)">
  <div class="abs head" style="left:132px;top:78px;font-size:18px;font-weight:600">IMPRESSIVE PEER CEOS</div>
  <div class="abs body-txt" style="left:132px;top:124px;width:270px">Join a diverse blend of 17 seasoned men and women CEOs from some of San Diego's finest companies. The group features award-winning private and venture-backed companies.</div>
  <div class="btn" style="left:132px;top:262px;width:145px;height:44px">Our Members ›</div>
  <div class="photo" style="left:532px;top:0;width:668px;height:403px;background:linear-gradient(150deg,#3c5a4a,#2c4a5e 45%,#3a3040 100%)" role="img" aria-label="Group photo of peer CEO members"></div>
</section>

<!-- Blog -->
<section class="abs" style="left:0;top:3021px;width:1200px;height:557px;background:var(--blue)">
  <div class="abs center head" style="top:48px;color:#fff;font-size:22px;font-weight:600">DEREK'S BLOG</div>
</section>
<article class="post" style="left:131px">
  <div class="img" style="background:linear-gradient(135deg,#5a3f2e,#8a6a50 50%,#3a3a3a)" role="img" aria-label="Team working around a wooden table with laptops"></div>
  <div class="in"><div class="date">January 12, 2020</div><h3>What Are OKRs and How Your Team Should Adopt Them</h3><p>It's easy to set goals, and hard to achieve them.  And, few people do.</p><div class="btn">Read More ›</div></div>
</article>
<article class="post" style="left:451px">
  <div class="img" style="background:linear-gradient(135deg,#e8e8ea,#9aa0a8 55%,#3e4450)" role="img" aria-label="Colleagues talking in a bright office"></div>
  <div class="in"><div class="date">January 12, 2020</div><h3>LUMORA Defines<br>Great Managers</h3><p>It's not every day you learn of a really smart company setting out to prove that...</p><div class="btn">Read More ›</div></div>
</article>
<article class="post" style="left:769px">
  <div class="img" style="background:linear-gradient(135deg,#f0f2f4,#b8c0c8 50%,#5d6670)" role="img" aria-label="Presenter addressing a meeting room"></div>
  <div class="in"><div class="date">January 12, 2020</div><h3>Competing for talent in 2019?<br>Ask yourself these 6 questions</h3><p>Now that there are more job openings than people to fill them, 2019 is the time to get</p><div class="btn">Read More ›</div></div>
</article>

<!-- Testimonials -->
<section class="abs" style="left:0;top:3578px;width:1200px;height:504px;background:linear-gradient(180deg,#eef0f4,#dfe3ea)" role="img" aria-label="Faded office background behind testimonials">
  <div class="abs center h2" style="top:54px">TESTIMONIALS</div>
  <div class="abs center" style="top:100px;font-size:48px;font-family:Georgia,serif;color:#333;line-height:48px">“</div>
  <svg width="16" height="28" class="abs" style="left:134px;top:270px"><path d="M14 2L3 14l11 12" stroke="#555" fill="none" stroke-width="2"/></svg>
  <svg width="16" height="28" class="abs" style="left:1050px;top:270px"><path d="M2 2l11 12L2 26" stroke="#555" fill="none" stroke-width="2"/></svg>
  <div class="abs" style="left:240px;top:196px;width:720px;text-align:center;font-size:17px;line-height:29px;color:#222">I sold my company for $61.5M and the second three years later for $176M. Considering a 6-year investment of about $86,000 the ROI is considerable. While that is substantial, I found the consistent executive leadership training, employee practices, directions, and adjacent CEO council the most significant. This proved instrumental in managing the high growth and preparing the staff and company towards embracing the impact to the culture as we navigated through the positive outcome.</div>
  <div class="abs" style="left:568px;top:382px;width:64px;height:2px;background:#333"></div>
  <div class="abs center" style="top:420px;font-size:14px;color:#222">Martin Halvers, CEO, Northfield Process Group</div>
</section>

<!-- Methodology -->
<section class="abs" style="left:0;top:4082px;width:1200px;height:490px;background:var(--navy)">
  <div class="abs head" style="left:130px;top:72px;color:#fff;font-size:23px;font-weight:500;line-height:33px">PROVEN PEERHOLD<br>METHODOLOGY</div>
  <div class="abs" style="left:130px;top:158px;width:350px;color:#e6ebf2;font-size:15px;line-height:22.5px">According to Calder &amp; Whitmore, in 2020 Peerhold member companies outperformed the competition and grew 4.6% compared to nonmember companies who shrunk -4.7% .<br><br>Not every CEO Peer Group, nor every Peerhold group, is the same. Learn why ours is different and find out if you might be a fit for our limited space.</div>
  <div class="btn" style="left:133px;top:354px;width:212px;height:44px">Membership Criteria ›</div>
  <div class="photo" style="left:511px;top:0;width:689px;height:490px;background:linear-gradient(135deg,#cfd6de,#8894a2 45%,#2b3546 80%)" role="img" aria-label="Businessman reviewing documents with a colleague at a desk"></div>
</section>

<!-- Footer -->
<footer class="abs" style="left:0;top:4572px;width:1200px;height:306px;background:var(--navy-deep)">
  <div class="abs" style="left:130px;top:40px">
    <div class="brand" style="color:#fff;font-size:52px;line-height:52px">PEERHOLD</div>
    <div class="brand-sub" style="color:#b8c6d8;font-size:13px;margin-left:6px;margin-top:4px">Private advisory boards for CEOs,<br>executives and business owners.</div>
  </div>
  <div class="abs head" style="left:548px;top:60px;color:#cfd8e4;font-size:11px">FOLLOW US</div>
  <div class="abs" style="left:640px;top:50px;width:32px;height:32px;border-radius:50%;background:var(--blue)"></div>
  <div class="btn" style="left:692px;top:44px;width:162px;height:44px">
    <svg width="12" height="12" viewBox="0 0 24 24" style="margin-right:8px"><path fill="#fff" d="M6.6 10.8a15 15 0 0 0 6.6 6.6l2.2-2.2c.3-.3.7-.4 1-.2 1.1.4 2.3.6 3.6.6.6 0 1 .4 1 1V20c0 .6-.4 1-1 1A17 17 0 0 1 3 4c0-.6.4-1 1-1h3.5c.6 0 1 .4 1 1 0 1.3.2 2.5.6 3.6.1.3 0 .7-.2 1z"/></svg>Contact Derek</div>
  <div class="abs" style="left:130px;top:210px;width:940px;height:1px;background:#29456a"></div>
  <div class="abs center" style="top:266px;color:#cfd8e4;font-size:11px">Copyright © 2022 All Rights Reserved</div>
</footer>
<nav class="fnav">
  <a>ABOUT THE GROUP</a><a>MEMBER VIDEO TESTIMONIALS</a><a>TESTIMONIALS</a><a>SUCCESS STORIES</a><a>DEREK'S BLOG</a><a>DEREK MULVANE BIO</a><a>JOIN THE GROUP</a>
</nav>

</body>
</html>
```